E-Book-Cover für einen Kriminalroman
Zielgruppe
Ich veröffentliche meinen Roman “Die Schwelle” als E-Book.
Das Buch spielt in einer nahen Zukunft, in der Die Schwelle Nachrichten in die Vergangenheit möglich macht. Unfälle und Straftaten werden sofort ungeschehen gemacht. Jeder Bürger kann seinem vergangenen Ich eine Botschaft schicken - und so die eigene Geschichte “reparieren”. Auch Henrik, ein unscheinbarer Projektleiter, erhält eines Tag eine Nachricht aus der Zukunft: 'Halte dich von Maren fern. Sie wird dein Untergang sein'. Die Nachricht stellt Henrik vor ein Rätsel. Vor welcher Gefahr hat er sich gewarnt? Und wer ist Maren? Ein Jahr später wird Henrik durch Zufall Mitwisser einer politischen Verschwörung. Die Killer machen Jagd auf ihn und kennen jeden seiner nächsten Schritte. Die letzte Rettung ist ausgerechnet eine Frau namens Maren.
--- “Die Schwelle” spielt in der Zukunft, ist aber kein Science Fiction Roman. Die beschriebene Welt ist (außer der Zeitmanipulation) wie die unsere. Am ehesten ist das Buch also ein actionreicher Kriminalroman.
Die Hauptzielgruppe sind 25 - 45-jährige, zum Beispiel Leser von Rolf Ebenhöch, Tobias Wendrath oder Karl Vossberg.
Aufgabenstellung
Gewünscht ist ein E-Book-Cover für die Verwendung auf Online-Plattformen wie Kaufora.
Autor: K.J. Brandau
Titel: Die Schwelle
Zusatz: Roman
Visuelle Anforderungen
Das Cover sollte eine Reihe von Türen zeigen. Begründung dazu: Im sogenannten Registerbüro muss der Protagonist in einer von vier nebeneinanderliegenden Türen treten und empfängt dort seine Nachricht aus der Zukunft. Das Thema “Entscheidungen fürs Leben” des Romans wird durch diese Türen visualisiert und als Symbol mehrmals aufgegriffen - dementsprechend ist es aus meiner Sicht perfekt für das Cover.
Für die Fotosuche: Das Registerbüro ist leicht heruntergekommen und wirkt kühl und unsympathisch. Dieses Bild https://de.bildquelle-beispiel.de/id/19384726 (auch noch einmal angehängt) zum Beispiel passt sehr gut.
Thema Hacking und Programmieren
Das Buch spielt in den Lebenswelten von Programmierern und Hackern; Die Schwelle ist eine Datenbank. Dies könnte durch Stil der Schrift oder anders unterstützt werden. Nur, wenn sinnvoll und ohne dass es wie ein Computerbuch aus den 90ern wirkt natürlich :)
- Die Font kann das Thema aufgreifen, aber bitte KEINE Vintage LED-Schrift im Stil von http://www.schriftkiste-beispiel.de/segment-alt.font, sondern eine die einem modernen Monitor entspringt. Entweder verpixelt (Beispiel im Anhang) oder durch eine gepunktete Schrift in hoher "Auflösung" (Beispiel: http://www.schriftkiste-beispiel.de/perlen-raster.font, also nicht nur 7 Punkte in der Breite), hier könnte man die Ränder auch etwas blurren, um den Effekt eines Monitors zu erzielen
- Wenn der o.g. Schriftstil benutzt wird, bitte in Kleinbuchstaben (wie ein Befehl auf dem Terminal)
-> All kein Muss, nur wenn sinnvoll!
Weitere Anforderungen:
- Die Türen befinden sich in einem kühlen, sterilen BÜRO, dementsprechend dürfen sie nicht zu hübsch aussehen oder an Wohnzimmertüren erinnern
- Wenn Codezeilen als Hintergrundbestandteil genutzt..

```html
<!DOCTYPE html>
<html lang="de">
<head>
<meta charset="utf-8">
<title>Die Schwelle – Cover-Varianten</title>
<link rel="stylesheet" href="https://fonts.googleapis.com/css2?family=Open+Sans:wght@400&family=Orbitron:wght@700&display=swap">
<style>
  :root {
    --page-bg: #ffffff;
    --night-top: #15212c;
    --night-mid: #0a1118;
    --night-low: #010203;
    --office-core: #86a6ae;
    --office-mid: #4f6a72;
    --office-edge: #1b272c;
    --floor: #3c4f56;
    --door-light: #eef1f2;
    --door-shade: #b9c3c7;
    --author-ink: #5f7180;
    --tagline-ink: #a9b9c6;
    --title-edge: #6f8e9a;
  }
  html, body {
    margin: 0;
    width: 1112px;
    height: 1200px;
    overflow: hidden;
    background: var(--page-bg);
  }
  .sheet {
    position: relative;
    width: 1112px;
    height: 1200px;
  }
  .cover {
    position: absolute;
    width: 478px;
    height: 765px;
    overflow: hidden;
    background: linear-gradient(180deg, var(--night-top) 0%, var(--night-mid) 40%, var(--night-low) 64%);
  }
  .cover--color { left: 52px; top: 58px; }
  .cover--mono { left: 587px; top: 58px; filter: grayscale(1) brightness(1.3) contrast(1.05); }
  .cover--mono .cover__author { color: #8f979d; }
  .cover--mono .cover__tagline { color: #f1f3f5; }
  .cover--thumb { left: 476px; top: 867px; transform: scale(0.349); transform-origin: 0 0; }

  .cover__code-glow {
    position: absolute;
    left: 0; top: 0;
    width: 100%; height: 380px;
    background: radial-gradient(ellipse at 40% 35%, rgba(70,95,115,0.35), rgba(0,0,0,0) 70%);
  }
  .cover__author {
    position: absolute;
    left: 0; right: 0;
    top: 44px;
    margin: 0;
    text-align: center;
    font-family: "Open Sans", sans-serif;
    font-weight: 400;
    font-size: 40px;
    letter-spacing: 0.5px;
    color: var(--author-ink);
  }
  .cover__title {
    position: absolute;
    left: 0; top: 0;
    width: 478px; height: 420px;
  }
  .cover__title text {
    font-family: "Orbitron", sans-serif;
    font-weight: 700;
    paint-order: stroke;
    stroke: var(--title-edge);
    stroke-width: 4px;
    stroke-linejoin: round;
  }
  .cover__tagline {
    position: absolute;
    left: 0; right: 0;
    top: 419px;
    margin: 0;
    text-align: center;
    font-family: "Open Sans", sans-serif;
    font-size: 19px;
    letter-spacing: 1px;
    color: var(--tagline-ink);
  }
  .cover__office {
    position: absolute;
    left: 0; top: 492px;
    width: 100%; height: 273px;
    background:
      linear-gradient(180deg, rgba(0,0,0,0) 0%, rgba(0,0,0,0) 72%, rgba(10,16,20,0.55) 100%),
      radial-gradient(ellipse 65% 55% at 50% 45%, var(--office-core), var(--office-mid) 60%, var(--office-edge) 100%);
  }
  .cover__doors {
    position: absolute;
    left: 0; top: 0;
    width: 478px; height: 273px;
  }
</style>
</head>
<body>
<main class="sheet">

  <article class="cover cover--color">
    <div class="cover__code-glow" role="img" aria-label="Unscharfe Spalten aus Binärziffern im dunklen Hintergrund"></div>
    <p class="cover__author">K.J. Brandau</p>
    <svg class="cover__title" viewBox="0 0 478 420" aria-label="Die Schwelle">
      <defs>
        <linearGradient id="titleFillA" x1="0" y1="0" x2="0" y2="1">
          <stop offset="0" stop-color="#ffffff"/>
          <stop offset="1" stop-color="#c9d2da"/>
        </linearGradient>
      </defs>
      <text x="123" y="298" font-size="56" textLength="92" lengthAdjust="spacingAndGlyphs" fill="url(#titleFillA)">DIE</text>
      <text x="56" y="398" font-size="84" textLength="362" lengthAdjust="spacingAndGlyphs" fill="url(#titleFillA)">SCHWELLE</text>
    </svg>
    <p class="cover__tagline">ROMAN</p>
    <div class="cover__office" role="img" aria-label="Kühler Büroraum mit vier weißen nebeneinanderliegenden Türen">
      <svg class="cover__doors" viewBox="0 0 478 273" aria-hidden="true">
        <defs>
          <linearGradient id="doorFillA" x1="0" y1="0" x2="0" y2="1">
            <stop offset="0" stop-color="#eef1f2"/>
            <stop offset="0.8" stop-color="#d3dadd"/>
            <stop offset="1" stop-color="#9fadb2"/>
          </linearGradient>
        </defs>
        <rect x="66" y="68" width="60" height="127" fill="url(#doorFillA)"/>
        <rect x="161" y="68" width="60" height="127" fill="url(#doorFillA)"/>
        <rect x="256" y="68" width="60" height="127" fill="url(#doorFillA)"/>
        <rect x="351" y="68" width="60" height="127" fill="url(#doorFillA)"/>
      </svg>
    </div>
  </article>

  <article class="cover cover--mono">
    <div class="cover__code-glow" role="img" aria-label="Unscharfe Spalten aus Binärziffern im dunklen Hintergrund"></div>
    <p class="cover__author">K.J. Brandau</p>
    <svg class="cover__title" viewBox="0 0 478 420" aria-label="Die Schwelle">
      <defs>
        <linearGradient id="titleFillB" x1="0" y1="0" x2="0" y2="1">
          <stop offset="0" stop-color="#ffffff"/>
          <stop offset="1" stop-color="#c9d2da"/>
        </linearGradient>
      </defs>
      <text x="123" y="298" font-size="56" textLength="92" lengthAdjust="spacingAndGlyphs" fill="url(#titleFillB)">DIE</text>
      <text x="56" y="398" font-size="84" textLength="362" lengthAdjust="spacingAndGlyphs" fill="url(#titleFillB)">SCHWELLE</text>
    </svg>
    <p class="cover__tagline">ROMAN</p>
    <div class="cover__office" role="img" aria-label="Kühler Büroraum mit vier weißen nebeneinanderliegenden Türen">
      <svg class="cover__doors" viewBox="0 0 478 273" aria-hidden="true">
        <defs>
          <linearGradient id="doorFillB" x1="0" y1="0" x2="0" y2="1">
            <stop offset="0" stop-color="#eef1f2"/>
            <stop offset="0.8" stop-color="#d3dadd"/>
            <stop offset="1" stop-color="#9fadb2"/>
          </linearGradient>
        </defs>
        <rect x="66" y="68" width="60" height="127" fill="url(#doorFillB)"/>
        <rect x="161" y="68" width="60" height="127" fill="url(#doorFillB)"/>
        <rect x="256" y="68" width="60" height="127" fill="url(#doorFillB)"/>
        <rect x="351" y="68" width="60" height="127" fill="url(#doorFillB)"/>
      </svg>
    </div>
  </article>

  <article class="cover cover--color cover--thumb">
    <div class="cover__code-glow" role="img" aria-label="Unscharfe Spalten aus Binärziffern im dunklen Hintergrund"></div>
    <p class="cover__author">K.J. Brandau</p>
    <svg class="cover__title" viewBox="0 0 478 420" aria-label="Die Schwelle">
      <defs>
        <linearGradient id="titleFillC" x1="0" y1="0" x2="0" y2="1">
          <stop offset="0" stop-color="#ffffff"/>
          <stop offset="1" stop-color="#c9d2da"/>
        </linearGradient>
      </defs>
      <text x="123" y="298" font-size="56" textLength="92" lengthAdjust="spacingAndGlyphs" fill="url(#titleFillC)">DIE</text>
      <text x="56" y="398" font-size="84" textLength="362" lengthAdjust="spacingAndGlyphs" fill="url(#titleFillC)">SCHWELLE</text>
    </svg>
    <p class="cover__tagline">ROMAN</p>
    <div class="cover__office" role="img" aria-label="Kühler Büroraum mit vier weißen nebeneinanderliegenden Türen">
      <svg class="cover__doors" viewBox="0 0 478 273" aria-hidden="true">
        <defs>
          <linearGradient id="doorFillC" x1="0" y1="0" x2="0" y2="1">
            <stop offset="0" stop-color="#eef1f2"/>
            <stop offset="0.8" stop-color="#d3dadd"/>
            <stop offset="1" stop-color="#9fadb2"/>
          </linearGradient>
        </defs>
        <rect x="66" y="68" width="60" height="127" fill="url(#doorFillC)"/>
        <rect x="161" y="68" width="60" height="127" fill="url(#doorFillC)"/>
        <rect x="256" y="68" width="60" height="127" fill="url(#doorFillC)"/>
        <rect x="351" y="68" width="60" height="127" fill="url(#doorFillC)"/>
      </svg>
    </div>
  </article>

</main>
</body>
</html>
```